Stationery Design Project for Marketing Consultancy

I have started a new consultancy business and require the following elements to be designed using existing logo:
• Business card
• Letterhead
• Envelope (DL, C4, C5)
• Microsoft word template for report writing
• A4 Presentation Folder
• Powerpoint template
COPY FOR FRONT AND BACK OF BUSINESS CARD
logo
'Measurable Marketing. Epic Results' slogan (but no need to use existing lockup with logo)
name, B Bus. Mktg, Grad Dip Digital Mktg, CPM (post nominal abbreviations in smaller font)
mobile: 04XX-XXX-XXX (I will give details to the winner to add)
website: www.tolvarin.com.au
email: info@tolvarin.com.au
COPY FOR LETTERHEAD
Logo
Company Name
Please, submit your designs that include business card, letterhead and envelope. Once selected the winner will be asked to complete the project by creating the rest of the artwork.
FINAL FILES
Print ready files to be supplied as well as Indesign files so that minor amends can be made if necessary in future.
• Layered vectors in EPS & PDF
• Screen quality JPEG & PNGs
ABOUT THE BUSINESS: TOLVARIN
I work with clients to understand their business challenges, developing and executing measurable marketing strategies tied to key business metrics. Services include:
Services include:
• Business planning and business development
• Marketing and brand strategy
• Insight-driven integrated campaigns
• Loyalty programs and retention marketing
• Marketing automation
• Direct marketing (traditional and digital)
• Content strategy and development
Hi everyone,
Target Market(s)
Corporate decision makers (heads of marketing, general managers etc) and small to medium sized business owners. Predominately male aged 35+
Industry/Entity Type
Marketing
Requirements
Must have
- BRAND PERSONALITY
The successful design will communicate brand personality. I am a professional, results-driven entrepreneur, but want to show off my creative flair.
MEMORABILITY
Looking for a unique and eye-catching design. Am considering special printing effects (die cuts, letterpress, interactive elements, embossing, foiling etc) or a striking minimalist approach.
Nice to have
- I have a mission that could be incorporated on reverse if room -
Turning insights into actions & passion into profit.
Should not have
- Use of pink or green.

```html
<!DOCTYPE html>
<html lang="en">
<head>
<meta charset="utf-8">
<title>Tolvarin Letterhead</title>
<link href="https://fonts.googleapis.com/css2?family=Questrial&display=swap" rel="stylesheet">
<style>
  :root {
    --paper: #ffffff;
    --ink: #4a4a4a;
    --ink-dark: #3a3a3a;
    --swoosh: #e2e2e2;
    --bubble: #f5f5f5;
    --band-top: #f7f7f7;
    --band-bottom: #dedede;
    --band-line: #d0d0d0;
  }
  * { margin: 0; padding: 0; box-sizing: border-box; }
  html, body {
    width: 848px;
    height: 1200px;
    overflow: hidden;
    background: var(--paper);
  }
  .letterhead {
    position: relative;
    width: 848px;
    height: 1200px;
    background: var(--paper);
    font-family: "Questrial", sans-serif;
    color: var(--ink);
    overflow: hidden;
  }
  .backdrop {
    position: absolute;
    inset: 0;
  }
  .brand {
    position: absolute;
    left: 130px;
    top: 10px;
    width: 160px;
    text-align: center;
  }
  .brand-mark {
    width: 66px;
    height: 66px;
    margin: 0 auto 10px;
    border-radius: 50%;
    background: var(--ink-dark);
  }
  .brand-name {
    font-size: 30px;
    letter-spacing: 0.5px;
    color: var(--ink-dark);
    line-height: 1;
  }
  .brand-slogan {
    margin-top: 6px;
    font-size: 7.6px;
    letter-spacing: 0.1px;
    color: var(--ink);
    white-space: nowrap;
  }
  .footer-band {
    position: absolute;
    left: 0;
    bottom: 0;
    width: 848px;
    height: 74px;
    background: linear-gradient(to bottom, var(--band-top), var(--band-bottom));
    border-top: 1px solid var(--band-line);
  }
  .contact {
    position: absolute;
    left: 74px;
    top: 25px;
    display: flex;
    align-items: center;
    font-size: 18px;
    color: var(--ink);
    white-space: nowrap;
  }
  .contact-badge {
    display: inline-flex;
    align-items: center;
    justify-content: center;
    width: 23px;
    height: 23px;
    border-radius: 50%;
    background: var(--ink-dark);
    color: var(--paper);
    font-size: 13px;
    margin: 0 6px 0 8px;
  }
  .contact-web {
    margin-left: 10px;
    font-size: 21px;
    letter-spacing: 0.4px;
  }
</style>
</head>
<body>
<main class="letterhead">
  <svg class="backdrop" width="848" height="1200" viewBox="0 0 848 1200" aria-hidden="true">
    <g class="swoosh" fill="none" stroke="var(--swoosh)">
      <path d="M0 108 C60 130 130 142 214 140 C400 134 560 30 712 38 C780 42 820 58 848 78" stroke-width="4"/>
      <path d="M0 100 C70 124 140 136 220 134 C410 126 565 26 715 32 C782 36 822 52 848 70" stroke-width="1.2"/>
    </g>
    <g class="bubbles" fill="var(--bubble)">
      <circle cx="258" cy="429" r="29"/>
      <circle cx="305" cy="516" r="47"/>
      <circle cx="228" cy="658" r="71"/>
      <circle cx="335" cy="826" r="94"/>
      <circle cx="135" cy="1012" r="138"/>
    </g>
  </svg>

  <header class="brand">
    <div class="brand-mark"></div>
    <div class="brand-name">TOLVARIN</div>
    <div class="brand-slogan">MEASURED STRATEGY. BOLD OUTCOMES.</div>
  </header>

  <footer class="footer-band">
    <div class="contact">
      <span class="contact-address">Address Line here 1 Address Line here 2</span>
      <span class="contact-badge">P</span>
      <span class="contact-phone">123-000-0000</span>
      <span class="contact-badge">W</span>
      <span class="contact-web">www.tolvarin.com.au</span>
    </div>
  </footer>
</main>
</body>
</html>
```